Hardcore nerd needs to stand out in a sea of dull Defence business cards

Wombarra Devices is a new Australian consulting engineering company that turns research and theory into practical systems. No evangelistic fluff, just mathematics and physics into electronic and optical circuits for consumer products, scientific research or Defence applications.

We already have a recognised logo (provided) which is often dark blue/black on a light background but we're open to other combinations. (Us engineers tend to have limited aesthetic imagination :)

Some of our recent products have included:
* Instrumentation for electrical testing,
* Radar jammers,
* GPS antenna design,
* Satellite tracking systems,
* High power lasers

We're open to both single and double-sided designs - happy to be convinced either way.

P.S. Another group is working on the web page, so - alas - our web site is currently of no use for images/ideas...

Target Market(s)

Engineering managers,
Scientists

Contact Information for Business Card

Dr Colin Harte
R&D Engineer

colin@wombarradevices.com.au
0427 563 710

PO Box XXX (to be confirmed)
Kelsby ACT 2917
Australia

Font styles to use
Serif
Sans Serif

Colors

Designer to choose colors to be used in the design.

Requirements
Must have
• My contact details!
• I've had many (great) "bold and plain" designs submitted already, so feel free to be artistically creative :)
• Happy to take advice re fonts/colours/printability etc.
Nice to have
• I'm not sure if "lists" are more at home on a CV than a business card, but representative services include:
• Applied electromagnetics
• RF and high speed electronics
• Signal and image processing
• Electro-optical and laser systems
• Concept-to-prototype design services
• If you're considering double sided cards, then often measuring/alignment grids/rulers feature on the back of similar cards.
• e.g. https://www.veltranoptics.example/newgrouppage9.cfm?objectgroup_id=4183
• https://www.veltranoptics.example/newgrouppage9.cfm?objectgroup_ID=4185
• ..or even a "Smith chart" (google will return lots)
• Generic images to represent a capability might work - googling images associated with keyword for each of these areas might help:
• - "passive radar", "phased array", "fdtd", "vircator"
• RF and high speed electronic design
• - "smith chart", "microstrip circuits", "dimensioned drawing", "electronic schematic"
• - "dft", "iir filter"
• - "optical cavity". "laser energy level diagram"
• Background/watermarked images outlines/wireframes/schematics would probably look OK.
Should not have
• If a list of projects/services is provided, it is important not to make the client feel that this is "all" the company can do. Engineering design is a creative discipline (like graphics :)
• Please, no stock "military" snaps like planes, missiles, etc!

```html
<!DOCTYPE html>
<html lang="en">
<head>
<meta charset="utf-8">
<title>Wombarra Devices — Business Card</title>
<link rel="stylesheet" href="https://fonts.googleapis.com/css2?family=Lato:wght@400;700&family=Open+Sans:wght@600;800&display=swap">
<style>
  :root {
    --navy: #0b1f66;
    --navy-soft: #16307e;
    --paper: #ffffff;
    --ink: #1c2240;
    --rule: #b9c2dc;
    --rule-dark: #3a519a;
    --stage: #2f2f2f;
  }
  * { box-sizing: border-box; margin: 0; padding: 0; }
  html, body { width: 1200px; height: 866px; overflow: hidden; }
  body {
    background: var(--stage);
    display: flex;
    align-items: center;
    justify-content: center;
    gap: 40px;
    font-family: "Lato", Arial, sans-serif;
  }
  .card {
    position: relative;
    width: 540px;
    height: 330px;
    overflow: hidden;
    box-shadow: 0 10px 24px rgba(0,0,0,0.45);
  }
  .card--front { background: var(--paper); color: var(--ink); }
  .card--back { background: linear-gradient(135deg, var(--navy-soft), var(--navy) 60%); color: var(--paper); }

  .brand { position: absolute; display: flex; align-items: center; gap: 12px; }
  .brand__dot { width: 64px; height: 64px; border-radius: 50%; flex: none; }
  .brand__name { font-family: "Open Sans", Arial, sans-serif; font-weight: 800; line-height: 1; }
  .brand__name span { display: block; }
  .brand__word { font-size: 30px; letter-spacing: 1px; }
  .brand__sub { font-size: 30px; letter-spacing: 1px; margin-top: 4px; }

  .card--front .brand { left: 232px; top: 74px; }
  .card--front .brand__dot { background: var(--navy); }
  .card--front .brand__name { color: var(--navy); }

  .contact { position: absolute; left: 36px; top: 150px; }
  .contact__name { font-family: "Open Sans", Arial, sans-serif; font-weight: 800; font-size: 19px; color: var(--navy); letter-spacing: 0.5px; }
  .contact__role { font-size: 15px; margin-bottom: 8px; }
  .contact__row { display: flex; align-items: center; gap: 8px; font-size: 14px; line-height: 22px; }
  .contact__row svg { width: 13px; height: 13px; fill: var(--navy); flex: none; }

  .rule { position: absolute; height: 1px; }
  .card--front .rule { left: 36px; right: 40px; top: 290px; background: var(--rule); }

  .card--back .brand { left: 50%; top: 80px; transform: translateX(-50%); }
  .card--back .brand__dot { background: var(--paper); }
  .card--back .brand__name { color: var(--paper); }

  .services {
    position: absolute; left: 44px; right: 44px; top: 198px;
    display: grid; grid-template-columns: 1fr 1fr; row-gap: 4px;
    list-style: none; font-size: 14px;
  }
  .services li::before { content: "•"; margin-right: 6px; }
  .card--back .rule { left: 44px; right: 44px; top: 260px; background: var(--rule-dark); }
</style>
</head>
<body>
  <section class="card card--front" aria-label="Card front">
    <div class="brand">
      <div class="brand__dot"></div>
      <div class="brand__name"><span class="brand__word">WOMBARRA</span><span class="brand__sub">DEVICES</span></div>
    </div>
    <div class="contact">
      <p class="contact__name">DR COLIN HARTE</p>
      <p class="contact__role">R&amp;D Engineer</p>
      <p class="contact__row">
        <svg viewBox="0 0 24 24" aria-hidden="true"><path d="M6.6 10.8a15 15 0 0 0 6.6 6.6l2.2-2.2a1 1 0 0 1 1-.25 11 11 0 0 0 3.6.6 1 1 0 0 1 1 1V20a1 1 0 0 1-1 1A17 17 0 0 1 3 4a1 1 0 0 1 1-1h3.5a1 1 0 0 1 1 1 11 11 0 0 0 .6 3.6 1 1 0 0 1-.25 1z"/></svg>
        0427 563 710
      </p>
      <p class="contact__row">
        <svg viewBox="0 0 24 24" aria-hidden="true"><path d="M2 5h20v14H2zm2 2v.5l8 5 8-5V7l-8 5z"/></svg>
        colin@wombarradevices.com.au
      </p>
      <p class="contact__row">
        <svg viewBox="0 0 24 24" aria-hidden="true"><path d="M12 2a7 7 0 0 0-7 7c0 5 7 13 7 13s7-8 7-13a7 7 0 0 0-7-7zm0 9.5A2.5 2.5 0 1 1 12 6.5a2.5 2.5 0 0 1 0 5z"/></svg>
        PO Box XXX Kelsby ACT 2917, Australia
      </p>
    </div>
    <div class="rule"></div>
  </section>

  <section class="card card--back" aria-label="Card back">
    <div class="brand">
      <div class="brand__dot"></div>
      <div class="brand__name"><span class="brand__word">WOMBARRA</span><span class="brand__sub">DEVICES</span></div>
    </div>
    <ul class="services">
      <li>Applied electromagnetics</li>
      <li>RF and high speed electronics</li>
      <li>Signal and image processing</li>
      <li>Electro-optical and laser systems</li>
    </ul>
    <div class="rule"></div>
  </section>
</body>
</html>
```